Business Card Design

Business Card for professional consulting firm working with large financial institutions.

Target Market(s)

Executive buyers

Industry/Entity Type

Banking

Contact Information for Business Card

Mild creativity wanted. Not boring, but do elaborate artwork.

Font styles to use
Serif
Sans Serif

Colors

Designer to choose colors to be used in the design.

Requirements
Must have
• Standard business card features - company name, individual name, telephone, website, email, locations.
Nice to have
• Two colors
Should not have
• too many colors, fancy printing, cartoons.

```html
<!DOCTYPE html>
<html lang="en">
<head>
<meta charset="utf-8">
<title>Novaledger Business Card</title>
<link rel="stylesheet" href="https://fonts.googleapis.com/css2?family=Roboto:wght@400;500&display=swap">
<style>
  :root {
    --backdrop: #d9d4cc;
    --card-light: #f4f4f4;
    --card-dark: #000000;
    --ink: #111111;
    --ink-soft: #3d3d3d;
    --ink-muted: #a9a9a9;
    --rule: #2a2a2a;
    --paper-white: #ffffff;
  }
  * { margin: 0; padding: 0; box-sizing: border-box; }
  html, body {
    width: 1200px;
    height: 960px;
    overflow: hidden;
    background: var(--backdrop);
    font-family: "Roboto", Arial, sans-serif;
  }
  .stage { position: relative; width: 1200px; height: 960px; }

  .card { position: absolute; width: 600px; height: 343px; }
  .card--front { left: 322px; top: 108px; background: var(--card-light); }
  .card--back { left: 320px; top: 493px; height: 342px; background: var(--card-dark); }

  .address-rule {
    position: absolute; left: 37px; top: 0; width: 2px; height: 100%;
    background: var(--rule);
  }
  .address {
    position: absolute; left: 21px; top: 310px;
    transform-origin: 0 0; transform: rotate(-90deg);
    white-space: nowrap; font-size: 12.5px; color: var(--ink-soft);
  }

  .holder { position: absolute; left: 58px; top: 30px; }
  .holder__name { font-size: 20px; font-weight: 500; color: var(--ink); letter-spacing: 0.2px; line-height: 1.1; }
  .holder__role { font-size: 14px; color: var(--ink-muted); margin-top: 2px; }

  .wordmark {
    position: absolute; font-weight: 400; white-space: nowrap;
  }
  .wordmark--front { left: 346px; top: 150px; font-size: 28px; color: var(--ink); }
  .wordmark--back { left: 0; width: 100%; text-align: center; top: 140px; font-size: 48px; color: var(--paper-white); }

  .contacts { position: absolute; left: 59px; top: 256px; list-style: none; }
  .contacts li {
    display: flex; align-items: center; gap: 7px;
    font-size: 14px; color: var(--ink-soft); height: 19.5px;
  }
  .contacts svg { width: 13px; height: 13px; fill: var(--ink); flex: none; }
</style>
</head>
<body>
<main class="stage">
  <section class="card card--front" aria-label="Business card front">
    <div class="address-rule"></div>
    <p class="address">4120 Harbor View Road, Juneau, Alaska 99801</p>

    <div class="holder">
      <h1 class="holder__name">DANIEL HART</h1>
      <p class="holder__role">CEO/FOUNDER</p>
    </div>

    <p class="wordmark wordmark--front">novaledger</p>

    <ul class="contacts">
      <li>
        <svg viewBox="0 0 16 16" aria-hidden="true"><path d="M3.6 1.2l2.3 2.6-1.3 2a9 9 0 0 0 5.6 5.6l2-1.3 2.6 2.3-1.2 2.3C7.5 16 0 8.5.9 2.4z"/></svg>
        555 210 4817
      </li>
      <li>
        <svg viewBox="0 0 16 16" aria-hidden="true"><path d="M1 3h14v1.2L8 8.6 1 4.2z"/><path d="M1 5.6l7 4.4 7-4.4V13H1z"/></svg>
        info@novaledger.com
      </li>
      <li>
        <svg viewBox="0 0 16 16" aria-hidden="true"><circle cx="8" cy="8" r="7"/><path d="M5 4.5c1.5.3 2 1.5 1.2 2.6-.8 1-2.2.7-2.5 2.3M10.5 3.2c-.4 1.3.6 2.1 1.8 1.9M9.5 12.5c.2-1.4 1.2-2 2.4-2.2" stroke="var(--card-light)" stroke-width="1.3" fill="none"/></svg>
        www.novaledger.com
      </li>
    </ul>
  </section>

  <section class="card card--back" aria-label="Business card back">
    <p class="wordmark wordmark--back">novaledger</p>
  </section>
</main>
</body>
</html>
```